TalkHarbor - Language Coaching Services

Sleek, innovative, trendy design for Language Coaching business.

TalkHarbor is a new UK based company that provides Language Coaching services. We offer highly personalized on-line and face to face language courses. We also impart learning techniques workshops based on the latest neuroscience research for second-language acquisition.

Target Market(s)

See attached info

Industry/Entity Type

Consulting

Contact Information for Business Card

TalkHarbor
DaniaKV@talkharbor.co.uk
TalkHarbor.co.uk
London, UK

Font styles to use
Sans Serif

```html
<!DOCTYPE html>
<html lang="en">
<head>
<meta charset="UTF-8">
<title>TalkHarbor Business Card</title>
<link href="https://fonts.googleapis.com/css2?family=Lato:wght@300;400;700;900&display=swap" rel="stylesheet">
<style>
  :root {
    --brand-blue: #0b96d1;
    --brand-blue-deep: #0a6fa6;
    --brand-blue-bright: #1aa6e0;
    --text-grey: #4a4f55;
    --divider: #a9d9ee;
    --card-white: #ffffff;
    --stage: #e6e8ea;
  }
  * { box-sizing: border-box; margin: 0; padding: 0; }
  html, body { width: 1200px; height: 782px; overflow: hidden; }
  body {
    background: var(--stage);
    font-family: "Lato", sans-serif;
    position: relative;
  }
  .card {
    position: absolute;
    width: 520px;
    height: 297px;
    box-shadow: 0 10px 30px rgba(0,0,0,0.18);
    overflow: hidden;
  }
  .card-front { left: 50px; top: 243px; background: var(--card-white); }
  .card-back  { left: 630px; top: 243px; background: var(--brand-blue); }

  .front-band {
    position: absolute; left: 0; right: 0; bottom: 0; height: 9px;
    background: linear-gradient(90deg, var(--brand-blue-bright), var(--brand-blue-deep));
  }
  .brand-block {
    position: absolute; left: 28px; top: 72px; width: 230px;
    display: flex; flex-direction: column; align-items: center;
  }
  .brand-mark {
    width: 74px; height: 74px; border-radius: 50%;
    border: 6px solid var(--brand-blue);
  }
  .brand-name {
    margin-top: 12px;
    font-size: 32px; font-weight: 400; letter-spacing: 1px;
    color: var(--brand-blue);
  }
  .divider {
    position: absolute; left: 272px; top: 70px; width: 1px; height: 130px;
    background: var(--divider);
  }
  .contact-block { position: absolute; left: 290px; top: 74px; color: var(--text-grey); }
  .person-name { font-size: 19px; color: var(--brand-blue); letter-spacing: 0.5px; }
  .person-name .first { font-weight: 900; }
  .person-name .last { font-weight: 300; }
  .person-role, .person-city { font-size: 14px; line-height: 18px; }
  .contact-list { list-style: none; margin-top: 12px; }
  .contact-list li {
    display: flex; align-items: center; gap: 7px;
    font-size: 14px; line-height: 19px;
  }
  .contact-list svg { width: 12px; height: 12px; flex: none; }

  .back-brand {
    position: absolute; right: 34px; bottom: 34px;
    display: flex; align-items: center; gap: 10px;
  }
  .back-mark {
    width: 46px; height: 46px; border-radius: 50%;
    border: 4px solid var(--card-white);
  }
  .back-name { font-size: 20px; font-weight: 400; color: var(--card-white); letter-spacing: 1px; }
</style>
</head>
<body>
  <section class="card card-front" aria-label="Business card front">
    <div class="brand-block">
      <div class="brand-mark"></div>
      <div class="brand-name">TALKHARBOR</div>
    </div>
    <div class="divider"></div>
    <div class="contact-block">
      <div class="person-name"><span class="first">MARCUS</span> <span class="last">HALE</span></div>
      <div class="person-role">Managing Director</div>
      <div class="person-city">London, UK</div>
      <ul class="contact-list">
        <li>
          <svg viewBox="0 0 12 12"><rect x="1" y="1" width="10" height="10" rx="2" fill="none" stroke="#0b96d1" stroke-width="1.6"/><rect x="4" y="4" width="4" height="4" fill="#0b96d1"/></svg>
          044 777 1234
        </li>
        <li>
          <svg viewBox="0 0 12 12"><rect x="0.5" y="2" width="11" height="8" fill="#0b96d1"/><path d="M0.5 2 L6 6.5 L11.5 2" fill="none" stroke="#fff" stroke-width="1"/></svg>
          DaniaKV@talkharbor.co.uk
        </li>
        <li>
          <svg viewBox="0 0 12 12"><circle cx="6" cy="6" r="5.5" fill="#0b96d1"/><path d="M0.5 6 H11.5 M6 0.5 C3 3 3 9 6 11.5 M6 0.5 C9 3 9 9 6 11.5" fill="none" stroke="#fff" stroke-width="0.8"/></svg>
          www.TalkHarbor.co.uk
        </li>
      </ul>
    </div>
    <div class="front-band"></div>
  </section>

  <section class="card card-back" aria-label="Business card back">
    <div class="back-brand">
      <div class="back-mark"></div>
      <div class="back-name">TALKHARBOR</div>
    </div>
  </section>
</body>
</html>
```